The Copperline Collective's website for high impact furniture promotions

I am looking for a simple website. we are a promotional company that runs events for furniture stores to increase sales for short periods of time. i would like the website to have about 4 areas to explain our company. I would like it to be simple and user friendly. I would like a link to chatterbook and a contact section. I am attaching our logo that i would like somewhere large or possibly in the backround. I am open to different color schemes. I would like to convey fast paced, modern, reliable. I am open to all different styles and look forward to seeing whats out there. we are looking for a quick turn around, so if we see one that we like quick, we will pick that one thanks
Reason: looking for some really creative designs and want to give a fair amount of time to produce
Target Market(s)
Retail Furniture store owners
Industry/Entity Type
It Company
Number of Pages Required
1 page
Colors
Designer to choose colors to be used in the design.
Look and feel

```html
<!DOCTYPE html>
<html lang="en">
<head>
<meta charset="utf-8">
<title>The Copperline Collective</title>
<link href="https://fonts.googleapis.com/css2?family=Open+Sans:wght@400;600;700&family=Playfair+Display:wght@400;700&display=swap" rel="stylesheet">
<style>
:root{
  --copper:#94673c;
  --copper-dark:#7a522d;
  --ink:#333333;
  --muted:#6f6f6f;
  --line:#d9d9d9;
  --paper:#ffffff;
  --mist:#efefef;
  --fog:#e2e2e2;
  --night:#2b2b2b;
}
*{box-sizing:border-box;margin:0;padding:0}
html,body{width:1200px;height:2852px;overflow:hidden;background:var(--paper)}
body{font-family:"Open Sans",Arial,sans-serif;color:var(--ink);position:relative}
a{text-decoration:none;color:inherit}

/* hero */
.hero{position:absolute;left:0;top:0;width:1200px;height:540px;overflow:hidden}
.hero-photo{position:absolute;inset:0;
  background:
    radial-gradient(ellipse 260px 200px at 200px 70px,rgba(245,240,230,.55),transparent 70%),
    radial-gradient(ellipse 300px 160px at 980px 60px,rgba(235,235,230,.45),transparent 70%),
    radial-gradient(ellipse 180px 260px at 390px 330px,rgba(196,170,140,.75),transparent 70%),
    radial-gradient(ellipse 140px 220px at 1090px 300px,rgba(150,40,40,.55),transparent 70%),
    radial-gradient(ellipse 420px 140px at 600px 470px,rgba(120,110,100,.6),transparent 70%),
    radial-gradient(ellipse 200px 120px at 120px 420px,rgba(170,60,60,.45),transparent 70%),
    linear-gradient(180deg,#9a9794 0%,#6e6a66 40%,#4d4844 75%,#3a3633 100%)}
.hero-shade{position:absolute;inset:0;background:rgba(25,22,20,.38)}
.hero-nav{position:absolute;top:0;left:0;width:100%;display:flex;justify-content:center;gap:4px}
.hero-nav a{color:#fff;font-size:15px;padding:14px 16px}
.hero-nav a.is-active{background:var(--copper)}
.hero-brand{position:absolute;left:0;width:100%;top:170px;text-align:center;color:#fff}
.brand-dot{display:inline-block;width:110px;height:110px;border-radius:50%;background:#fff;border:4px solid var(--copper)}
.hero-brand .brand-name{font-family:"Playfair Display",Georgia,serif;font-size:30px;letter-spacing:2px;margin-top:14px}
.hero-brand .brand-tag{font-size:11px;letter-spacing:3px;text-transform:uppercase;margin-top:6px;opacity:.9}

/* main nav */
.site-bar{position:absolute;top:560px;left:120px;width:980px;height:90px;display:flex;align-items:center;justify-content:space-between}
.bar-brand{display:flex;align-items:center;gap:10px}
.bar-brand .brand-dot{width:40px;height:40px;border-width:3px;background:var(--copper)}
.bar-brand span{font-family:"Playfair Display",Georgia,serif;font-size:17px;color:var(--copper-dark);width:130px;line-height:1.2}
.site-nav{display:flex;gap:30px;font-size:15px;color:var(--copper-dark)}

/* about */
.about{position:absolute;top:680px;left:160px;width:900px;height:300px}
.about-photo{position:absolute;left:0;top:0;width:420px;height:300px;border:1px solid var(--line);
  background:
    radial-gradient(ellipse 110px 80px at 280px 210px,rgba(255,255,255,.95),transparent 70%),
    radial-gradient(ellipse 40px 50px at 140px 170px,rgba(214,120,90,.55),transparent 70%),
    radial-gradient(ellipse 120px 30px at 200px 280px,rgba(190,170,140,.55),transparent 70%),
    linear-gradient(180deg,#f6f6f4 0%,#ececea 60%,#d8d6d0 100%)}
.about-copy{position:absolute;left:445px;top:0;width:455px}
.about-copy h2{font-family:"Playfair Display",Georgia,serif;color:var(--copper);font-size:30px;margin-bottom:12px}
.about-copy p{font-size:12.5px;line-height:2;color:var(--muted)}
.btn{display:inline-block;background:var(--copper);color:#fff;font-size:11px;letter-spacing:1px;padding:8px 16px;text-transform:uppercase}
.about-copy .btn{margin-top:16px}

/* section titles */
.section-title{text-align:center;font-size:20px;font-weight:600;color:var(--copper-dark);letter-spacing:1px;text-transform:uppercase}
.section-title::after{content:"";display:block;width:50px;height:2px;background:var(--copper);margin:8px auto 0}

/* services */
.services{position:absolute;top:1000px;left:0;width:1200px;height:360px;background:var(--mist);padding-top:40px}
.tabs{display:flex;justify-content:center;margin-top:34px}
.tabs a{font-size:14px;padding:16px 22px;text-transform:uppercase;color:var(--ink);background:#f7f7f7;border:1px solid var(--line)}
.tabs a.is-active{background:var(--copper);color:#fff;border-color:var(--copper)}
.services p{width:960px;margin:28px auto 0;text-align:center;font-size:13px;line-height:2;color:var(--muted)}

/* testimonials */
.testimonials{position:absolute;top:1380px;left:0;width:1200px;height:380px;background:var(--fog);padding-top:40px}
.quotes{display:flex;justify-content:center;gap:70px;margin-top:44px}
.quote{display:flex;gap:22px;width:400px}
.avatar{flex:none;width:84px;height:84px;border-radius:50%;background:radial-gradient(circle at 40% 35%,#d2b49a,#8a6a52 70%,#5e4838)}
.quote blockquote{font-family:"Playfair Display",Georgia,serif;font-size:14px;line-height:1.7;color:var(--ink)}
.quote cite{display:block;font-style:normal;font-size:13px;margin-top:8px}
.dots{display:flex;justify-content:center;gap:8px;margin-top:40px}
.dots span{width:12px;height:12px;border-radius:50%;border:2px solid var(--copper)}
.dots span.is-on{background:var(--copper)}

/* gallery */
.gallery-title{position:absolute;top:1776px;left:0;width:1200px}
.gallery{position:absolute;top:1832px;left:120px;width:960px;height:590px}
.tile{position:absolute;overflow:hidden}
.tile-offer{left:0;top:0;width:360px;height:280px;color:#fff;padding:64px 30px;
  background:
    linear-gradient(rgba(30,20,22,.55),rgba(30,20,22,.55)),
    radial-gradient(ellipse 140px 90px at 80px 60px,rgba(200,60,90,.7),transparent 70%),
    radial-gradient(ellipse 160px 100px at 290px 230px,rgba(150,110,90,.8),transparent 70%),
    linear-gradient(135deg,#5a3a40,#3d2a2c)}
.tile-offer .kicker{font-size:13px;letter-spacing:1px;text-transform:uppercase}
.tile-offer .headline{font-size:23px;font-weight:700;margin:8px 0 18px;text-transform:uppercase;white-space:nowrap}
.t2{left:368px;top:0;width:296px;height:280px;background:
    radial-gradient(ellipse 150px 60px at 150px 40px,rgba(240,235,220,.7),transparent 70%),
    radial-gradient(ellipse 120px 80px at 90px 220px,rgba(90,70,60,.7),transparent 70%),
    radial-gradient(ellipse 110px 70px at 230px 200px,rgba(180,150,120,.7),transparent 70%),
    linear-gradient(180deg,#b1a89c,#6e6055)}
.t3{left:672px;top:0;width:288px;height:280px;background:
    radial-gradient(ellipse 130px 60px at 140px 40px,rgba(245,230,210,.7),transparent 70%),
    radial-gradient(ellipse 110px 70px at 80px 180px,rgba(160,50,45,.8),transparent 70%),
    radial-gradient(ellipse 120px 80px at 220px 220px,rgba(210,180,150,.8),transparent 70%),
    linear-gradient(180deg,#c7a583,#7f4a36)}
.t4{left:0;top:288px;width:248px;height:300px;background:
    radial-gradient(ellipse 80px 60px at 110px 120px,rgba(120,150,110,.55),transparent 70%),
    radial-gradient(ellipse 110px 60px at 124px 220px,rgba(255,255,255,.95),transparent 70%),
    linear-gradient(180deg,#ffffff,#e6e7e4 70%,#cfd0cb)}
.t5{left:256px;top:288px;width:312px;height:300px;background:
    radial-gradient(ellipse 70px 130px at 90px 170px,rgba(60,55,55,.6),transparent 70%),
    radial-gradient(ellipse 70px 130px at 220px 170px,rgba(80,70,65,.55),transparent 70%),
    radial-gradient(ellipse 150px 50px at 156px 40px,rgba(250,248,240,.8),transparent 70%),
    linear-gradient(180deg,#ddd6cc,#a89a8a)}
.t6{left:576px;top:288px;width:384px;height:300px;background:
    radial-gradient(ellipse 170px 90px at 190px 210px,rgba(220,200,180,.9),transparent 70%),
    radial-gradient(ellipse 90px 80px at 300px 110px,rgba(170,60,70,.5),transparent 70%),
    radial-gradient(ellipse 120px 60px at 100px 60px,rgba(245,235,220,.7),transparent 70%),
    linear-gradient(180deg,#c9a58c,#9b6e55)}

/* contact */
.contact{position:absolute;top:2446px;left:0;width:1200px}
.contact-form{width:660px;margin:34px auto 0}
.field-row{display:flex;gap:40px}
.field{flex:1;border-bottom:1px solid var(--line);height:38px;font-size:12px;color:#999;display:flex;align-items:flex-end;padding-bottom:6px}
.field-wide{margin-top:16px;height:48px}
.contact-form .btn{display:block;width:90px;margin:22px auto 0;text-align:center}

/* footer */
.site-footer{position:absolute;left:0;top:2722px;width:1200px;height:130px;background:#f3f3f3}
.footer-brand{position:absolute;left:0;top:0;width:320px;height:130px;background:var(--night);
  clip-path:polygon(0 0,100% 0,82% 100%,0 100%);display:flex;flex-direction:column;align-items:center;justify-content:center;padding-right:60px;color:#fff}
.footer-brand .brand-dot{width:40px;height:40px;border-width:3px}
.footer-brand span{font-family:"Playfair Display",Georgia,serif;font-size:15px;margin-top:6px}
.footer-nav{position:absolute;right:110px;top:36px;display:flex;gap:26px;font-size:15px;color:var(--night);align-items:center}
.social{width:30px;height:30px;border-radius:50%;border:2px solid var(--night)}
.copyright{position:absolute;right:110px;top:76px;font-size:11px;color:var(--muted)}
</style>
</head>
<body>

<header class="hero">
  <div class="hero-photo" role="img" aria-label="Photo of a shopper carrying a cushion in a large furniture showroom"></div>
  <div class="hero-shade"></div>
  <nav class="hero-nav">
    <a class="is-active" href="#">Home</a><a href="#">About Us</a><a href="#">Services</a><a href="#">Products</a><a href="#">Promotions</a><a href="#">Contact Us</a>
  </nav>
  <div class="hero-brand">
    <span class="brand-dot"></span>
    <div class="brand-name">The Copperline Collective</div>
    <div class="brand-tag">High Impact Furniture Promotions</div>
  </div>
</header>

<div class="site-bar">
  <div class="bar-brand"><span class="brand-dot"></span><span>The Copperline Collective</span></div>
  <nav class="site-nav">
    <a href="#">Home</a><a href="#">About Us</a><a href="#">Services</a><a href="#">Products</a><a href="#">Promotions</a><a href="#">Contact Us</a>
  </nav>
</div>

<section class="about">
  <div class="about-photo" role="img" aria-label="Photo of a bright white living room with an armchair, side table and a vase of tulips"></div>
  <div class="about-copy">
    <h2>About Us</h2>
    <p>We help furniture retailers move more stock in less time. Our team plans, staffs and runs short, high energy sale events that bring new buyers through the door and turn browsing into buying. From the first plan to the final tally, we handle every detail so store owners can focus on their floor, their staff and their customers while sales climb fast.</p>
    <a class="btn" href="#">Read More</a>
  </div>
</section>

<section class="services">
  <h2 class="section-title">Our Services</h2>
  <div class="tabs">
    <a class="is-active" href="#">Furniture Store</a><a href="#">Events</a><a href="#">Promotions</a><a href="#">Short Time Sale</a>
  </div>
  <p>For furniture stores we build complete promotion programs around one clear goal: more sales in a short window. We study your inventory, set the right offers, train your staff and bring the crowd with targeted advertising. Each event is measured day by day so you always know what is working and where the next win will come from.</p>
</section>

<section class="testimonials">
  <h2 class="section-title">Testimonials</h2>
  <div class="quotes">
    <div class="quote">
      <div class="avatar" role="img" aria-label="Portrait of a client"></div>
      <blockquote>"Nam sum nun dolor in reprehenderit in voluptate velit esse cillum dolore eu fugiat nulla pariatur. Excepteur sint occaecat cupidatat non proident sunt in culpa qui officia deserunt mollit anim id est laborum."<cite>- Walter</cite></blockquote>
    </div>
    <div class="quote">
      <div class="avatar" role="img" aria-label="Portrait of a client"></div>
      <blockquote>"Nam sum nun dolor in reprehenderit in voluptate velit esse cillum dolore eu fugiat nulla pariatur. Excepteur sint occaecat cupidatat non proident sunt in culpa qui officia deserunt mollit anim id est laborum."<cite>- Jenna</cite></blockquote>
    </div>
  </div>
  <div class="dots"><span class="is-on"></span><span></span><span></span></div>
</section>

<h2 class="section-title gallery-title">Our Gallery</h2>
<section class="gallery">
  <div class="tile tile-offer" role="img" aria-label="Showroom photo behind a limited offer banner">
    <div class="kicker">Limited Offer</div>
    <div class="headline">100% Guaranteed Sale</div>
    <a class="btn" href="#">Read More</a>
  </div>
  <div class="tile t2" role="img" aria-label="Photo of a busy furniture store sale floor"></div>
  <div class="tile t3" role="img" aria-label="Photo of sofas displayed in a showroom"></div>
  <div class="tile t4" role="img" aria-label="Photo of a white sideboard with a plant"></div>
  <div class="tile t5" role="img" aria-label="Photo of sales staff talking with customers"></div>
  <div class="tile t6" role="img" aria-label="Photo of a couple choosing a sofa"></div>
</section>

<section class="contact">
  <h2 class="section-title">Contact Us</h2>
  <form class="contact-form">
    <div class="field-row"><div class="field">Name</div><div class="field">Email</div></div>
    <div class="field field-wide">Message</div>
    <a class="btn" href="#">Submit</a>
  </form>
</section>

<footer class="site-footer">
  <div class="footer-brand"><span class="brand-dot"></span><span>The Copperline Collective</span></div>
  <nav class="footer-nav">
    <a href="#">Home</a><a href="#">About Us</a><a href="#">Services</a><a href="#">Products</a><a href="#">Promotions</a><a href="#">Contact Us</a>
    <a class="social" href="#" aria-label="chatterbook"></a>
  </nav>
  <div class="copyright">© 2017, All rights reserved | www.copperlinecollective.com</div>
</footer>

</body>
</html>
```